Powerpoint to present for client our social media services along with a test case

we need a powerpoint template design that is modern looking and eye catching and keeps the client engaged. we are a social media agency based in Kuwait so the content will be bilingual in english and in Arabic. i will be providing the logo and you can design based upon the logo provided. the main tasks for this PPT is to show case our case studies and for sales presentation. the presentations will be a mix of visuals, texts, graphs and charts.
the ppt design has to reflect the company colors in the logo with the logo scattered to show it is done by the company.

Industry/Entity Type

It Company

```html
<!DOCTYPE html>
<html lang="en">
<head>
<meta charset="utf-8">
<title>Sed et mi placerat odio auctor</title>
<link rel="stylesheet" href="https://fonts.googleapis.com/css2?family=Poppins:wght@600;700&family=Questrial&display=swap">
<style>
  :root {
    --sidebar: #2b2c37;
    --accent-green: #7cc243;
    --accent-light-green: #a6d34a;
    --accent-cyan: #19c4f2;
    --blue-top: #3c98de;
    --blue-bottom: #2f84cc;
    --lime-top: #c2dc3a;
    --lime-bottom: #abcb2f;
    --pill-green: #7dc242;
    --pill-cyan: #58c1f0;
    --ink: #111111;
    --muted: #6d6d6d;
    --dash: #8a8a8a;
    --white: #ffffff;
  }
  * { box-sizing: border-box; margin: 0; padding: 0; }
  html, body { width: 1200px; height: 675px; overflow: hidden; }
  body {
    position: relative;
    font-family: "Questrial", "Century Gothic", sans-serif;
    background: radial-gradient(ellipse at 55% 40%, #ffffff 0%, #f3f3f3 55%, #e4e4e4 100%);
    color: var(--ink);
  }
  .sidebar {
    position: absolute; left: 0; top: 0;
    width: 65px; height: 675px;
    background: var(--sidebar);
  }
  .corner-mark { position: absolute; left: 0; top: 0; }
  .brand {
    position: absolute;
    left: 32px; top: 580px;
    transform: translate(-50%, -50%) rotate(-90deg);
    white-space: nowrap;
    color: var(--white);
    font-size: 17px; letter-spacing: 3px;
  }
  .kicker {
    position: absolute; left: 145px; top: 43px;
    font-size: 12.5px; color: var(--muted);
  }
  .title {
    position: absolute; left: 143px; top: 62px;
    font-family: "Poppins", "Century Gothic", sans-serif;
    font-weight: 700; font-size: 44.5px; letter-spacing: -0.3px;
    line-height: 1.1; white-space: nowrap;
  }
  .subtitle {
    position: absolute; left: 145px; top: 126px;
    font-size: 28.5px; color: #1a1a1a; white-space: nowrap;
  }
  .diagram { position: absolute; left: 0; top: 0; }
  .node {
    position: absolute;
    display: flex; align-items: center; justify-content: center;
    text-align: center; color: var(--white);
  }
  .node-circle { width: 197px; height: 197px; border-radius: 50%; font-size: 21px; line-height: 1.45; }
  .node-start { left: 160px; top: 312px; background: linear-gradient(160deg, var(--blue-top), var(--blue-bottom)); }
  .node-end { left: 926px; top: 312px; background: linear-gradient(160deg, var(--lime-top), var(--lime-bottom)); }
  .node-pill { width: 370px; border-radius: 90px; font-size: 17.5px; line-height: 1.5; }
  .pill-upper { left: 464px; top: 204px; height: 167px; background: var(--pill-green); }
  .pill-lower { left: 464px; top: 407px; height: 181px; background: var(--pill-cyan); }
  .footer-meta {
    position: absolute; right: 104px; top: 605px;
    text-align: right; line-height: 1.2;
  }
  .footer-date { font-family: "Poppins", sans-serif; font-weight: 600; font-size: 13px; color: #5a5a5a; }
  .footer-url { font-size: 14px; color: var(--muted); }
  .footer-divider {
    position: absolute; left: 1109px; top: 604px;
    width: 1px; height: 38px; background: #b5b5b5;
  }
  .page-number {
    position: absolute; left: 1120px; top: 596px;
    font-family: "Poppins", sans-serif; font-weight: 700;
    font-size: 34px; color: #6a6a6a;
  }
</style>
</head>
<body>
  <aside class="sidebar">
    <svg class="corner-mark" width="80" height="115" viewBox="0 0 80 115" aria-hidden="true">
      <polygon points="0,0 112,0 0,66" fill="var(--accent-green)"/>
      <polygon points="0,0 40,0 0,24" fill="var(--accent-light-green)"/>
      <polygon points="18,56 79,36 79,113" fill="var(--accent-cyan)"/>
    </svg>
    <div class="brand">BRIGHTFIELD</div>
  </aside>

  <p class="kicker">BUILDING BRANDS THROUGH COMMUNITIES</p>
  <h1 class="title">Sed et mi placerat odio auctor</h1>
  <p class="subtitle">Aenean dictum tortor euismod magna faucibus, tincidunt&nbsp; congue</p>

  <svg class="diagram" width="1200" height="675" viewBox="0 0 1200 675" aria-hidden="true">
    <g fill="none" stroke="var(--dash)" stroke-width="2" stroke-dasharray="6 5">
      <path d="M381 406 H410 M410 300 V500 M410 300 H454 M410 500 H454"/>
      <path d="M835 302 H879 M835 500 H879 M879 302 V500 M879 406 H906"/>
    </g>
  </svg>

  <div class="node node-circle node-start">Lorem Ipsum is<br>simply dummy</div>
  <div class="node node-pill pill-upper">Contrary to popular belief,<br>Lorem Ipsum is not simply<br>random text. It has roots in a<br>piece of classical Latin literature<br>from 45 BC, making it over 2000</div>
  <div class="node node-pill pill-lower">There are many variations of<br>passages of Lorem Ipsum avail-<br>able, but the majority have suf-<br>fered alteration in some form, by<br>injected humour.</div>
  <div class="node node-circle node-end">Lorem Ipsum is<br>simply dummy</div>

  <div class="footer-meta">
    <p class="footer-date">March 24, 2014</p>
    <p class="footer-url">www.brightfieldco.com</p>
  </div>
  <div class="footer-divider"></div>
  <div class="page-number">6</div>
</body>
</html>
```